New Company Business Card design

Looking for a corporate looking business card utilising my new logo design - the logo i would like embossed as one option and flat as another - simplistic but stylish - less is more - we are an import export business launching into the market - i would like a couple of options as main background - Grey or Black

```html
<!DOCTYPE html>
<html lang="en">
<head>
<meta charset="utf-8">
<title>Meridian Trade Partners – Business Card</title>
<link href="https://fonts.googleapis.com/css2?family=Lato:wght@400;700&display=swap" rel="stylesheet">
<style>
  :root {
    --backdrop: #2b2b2d;
    --card: #1e1e20;
    --ink-light: #f2f2f2;
    --ink-muted: #8c8c90;
    --accent: #2e86cf;
    --divider: #6a6a6e;
  }
  * { margin: 0; padding: 0; box-sizing: border-box; }
  html, body { width: 1200px; height: 900px; overflow: hidden; }
  body {
    background: var(--backdrop);
    font-family: "Lato", sans-serif;
    position: relative;
  }
  .card {
    position: absolute;
    left: 250px;
    width: 700px;
    height: 400px;
    background: var(--card);
    box-shadow: 0 12px 30px rgba(0,0,0,0.45);
    overflow: hidden;
  }
  .card--front { top: 40px; }
  .card--back { top: 460px; }

  .brand {
    display: flex;
    align-items: center;
    gap: 12px;
    font-weight: 700;
    letter-spacing: 0.06em;
    text-transform: uppercase;
    white-space: nowrap;
  }
  .brand__mark {
    width: 22px; height: 22px;
    border-radius: 50%;
    flex: none;
  }
  .card--front .brand {
    position: absolute;
    left: 0; right: 0; top: 0; bottom: 0;
    justify-content: center;
    font-size: 30px;
    color: var(--ink-muted);
  }
  .card--front .brand__mark { background: var(--ink-muted); }

  .card--back .brand {
    position: absolute;
    left: 40px; top: 186px;
    font-size: 16px;
    color: var(--accent);
  }
  .card--back .brand__mark { background: var(--accent); width: 16px; height: 16px; }

  .divider {
    position: absolute;
    left: 376px; top: 90px;
    width: 2px; height: 220px;
    background: var(--divider);
  }
  .contact {
    position: absolute;
    left: 402px; top: 94px;
    right: 30px;
    color: var(--ink-light);
  }
  .contact__name {
    font-size: 22px;
    font-weight: 700;
    color: var(--accent);
  }
  .contact__role {
    font-size: 16px;
    margin-top: 2px;
  }
  .contact__address {
    font-size: 17px;
    line-height: 1.35;
    margin-top: 20px;
    font-style: normal;
  }
  .contact__list {
    list-style: none;
    margin-top: 18px;
    font-size: 17px;
  }
  .contact__list li {
    display: flex;
    align-items: center;
    gap: 12px;
    margin-bottom: 6px;
    white-space: nowrap;
  }
  .contact__icon { width: 17px; height: 17px; flex: none; }
</style>
</head>
<body>
  <section class="card card--front">
    <div class="brand"><span class="brand__mark"></span>Meridian Trade Partners</div>
  </section>

  <section class="card card--back">
    <div class="brand"><span class="brand__mark"></span>Meridian Trade Partners</div>
    <div class="divider"></div>
    <div class="contact">
      <div class="contact__name">Daniel Whitford</div>
      <div class="contact__role">Teaching Pastor</div>
      <address class="contact__address">412 N Harbor Avenue<br>Lakeview, MS 39100</address>
      <ul class="contact__list">
        <li>
          <svg class="contact__icon" viewBox="0 0 24 24" aria-hidden="true"><path fill="#2e86cf" d="M6.6 10.8a15.1 15.1 0 0 0 6.6 6.6l2.2-2.2c.3-.3.7-.4 1-.2 1.1.4 2.300.6 3.600.6.6 0 1 .4 1 1V20c0 .6-.4 1-1 1A17 17 0 0 1 3 4c0-.6.4-1 1-1h3.5c.6 0 1 .4 1 1 0 1.3.2 2.5.6 3.6.1.3 0 .7-.2 1z"/></svg>
          5550142288
        </li>
        <li>
          <svg class="contact__icon" viewBox="0 0 24 24" aria-hidden="true"><rect x="2.5" y="5" width="19" height="14" fill="none" stroke="#2e86cf" stroke-width="2"/><path d="M3 6l9 7 9-7" fill="none" stroke="#2e86cf" stroke-width="2"/></svg>
          dwhitford@meridiantrade.com
        </li>
        <li>
          <svg class="contact__icon" viewBox="0 0 24 24" aria-hidden="true"><g fill="none" stroke="#2e86cf" stroke-width="1.8"><circle cx="12" cy="12" r="9.5"/><ellipse cx="12" cy="12" rx="4.2" ry="9.5"/><path d="M2.5 12h19M4 7h16M4 17h16"/></g></svg>
          www.meridiantrade.com
        </li>
      </ul>
    </div>
  </section>
</body>
</html>
```